Landing Page and Logo for Auto-Blogging Platform

I created a platform that allows users to start a blog for their business, hobby, charity, etc. I need a landing page where users can learn about the platform, benefits of consistent blogging, SEO value, plans/pricing, etc. The landing page needs to have multiple call to action buttons encouraging the visitor to register/sign up for a free trial.

In addition to the landing page, I need a page for users to establish the settings for their blog. This page should be a fairly simple form, intended for the user to enter a few details to set up their blog:
1. Name of Blog
2. Up to 10 topics and/or keywords the blog should focus on
3. Theme: Color-scheme and logo upload for blog.

I have attached the specifications of the platform's functionality so you can better understand how it works, plans/pricing, etc.

I also need a logo for the business. The name of the platform is PostNook.

Target Market(s)

Website owners, bloggers, business owners

Industry/Entity Type

Technology, Internet, web design

Coding

Coded - Design and coding required

Number of Pages Required

2 page

Colors
0054AA
0677BA
7BADD7
CADEEF
E8F1F8
0094D4
00A9DD
6FCCEA
C7EBF8
E9F6FB

Requirements
Must have
• Eye-catching design but fairly light on content (keep it simple and brief.)
Nice to have
• Eye-catching yet simple design, clean and easy to understand what we are offering.
Should not have
• Too much “wordy” and confusing content.

```html
<!DOCTYPE html>
<html lang="en">
<head>
<meta charset="utf-8">
<title>PostNook – Auto-Blogging Platform</title>
<link rel="stylesheet" href="https://fonts.googleapis.com/css2?family=Lexend:wght@400;500;600&family=Inter:wght@400;500;600;700&display=swap">
<style>
:root{
  --navy:#0054AA;
  --blue:#0677BA;
  --sky:#0094D4;
  --cyan:#00A9DD;
  --card:#4BB3E3;
  --pale:#E8F1F8;
  --ice:#E9F6FB;
  --ink:#2b2f36;
  --muted:#5b6068;
  --white:#ffffff;
  --footer:#15181c;
}
*{margin:0;padding:0;box-sizing:border-box}
html,body{width:1200px;height:3568px;overflow:hidden}
body{font-family:"Inter",sans-serif;color:var(--ink);background:var(--white);position:relative}
.abs{position:absolute}
.display{font-family:"Lexend",sans-serif;font-weight:400;letter-spacing:.5px}

/* header */
.site-header{left:0;top:0;width:1200px;height:84px;background:var(--white)}
.brand{display:flex;align-items:center;gap:10px;font-family:"Lexend",sans-serif;font-weight:500;font-size:28px;color:var(--navy);white-space:nowrap}
.brand-dot{width:34px;height:34px;border-radius:50%;border:5px solid var(--sky);flex:none}
.header-brand{left:144px;top:23px}
.nav a{position:absolute;top:33px;font-size:14px;color:var(--ink);text-decoration:none;letter-spacing:.3px}
.nav a.active{color:var(--sky)}
.nav .active-bar{position:absolute;left:446px;top:0;width:42px;height:3px;background:var(--sky)}
.btn-outline{display:flex;align-items:center;justify-content:center;border:2px solid var(--navy);border-radius:22px;font-size:13px;font-weight:600;color:var(--ink);background:var(--white);letter-spacing:.3px}
.quote{left:927px;top:22px;width:128px;height:38px}

/* hero */
.hero{left:0;top:84px;width:1200px;height:560px;background:linear-gradient(120deg,#5b5a4e 0%,#8a8a80 30%,#3d4a52 60%,#1f2a2e 100%)}
.hero-box{left:324px;top:441px;width:552px;height:203px;background:var(--navy);text-align:center}
.hero-title{position:absolute;left:0;right:0;top:40px;font-size:72px;color:var(--white);font-weight:500}
.hero-cta{left:171px;top:130px;width:216px;height:37px;border:2px solid var(--white);border-radius:20px;color:var(--white);font-size:13px;font-weight:700;display:flex;align-items:center;justify-content:center}
.slide-arrow{left:1133px;width:32px;height:32px;border-radius:50%;background:var(--white);display:flex;align-items:center;justify-content:center}

/* about */
.about-photo{left:168px;top:744px;width:408px;height:408px;border-radius:50%;background:radial-gradient(circle at 55% 45%,#e6a23a 0%,#c88b3f 25%,#8a6a4c 55%,#4e3e34 100%)}
.about-title{left:630px;top:772px;font-size:50px;color:var(--ink)}
.about-text{left:630px;top:840px;width:425px;font-size:14.5px;line-height:24px;color:var(--muted);text-align:justify}
.about-text p+p{margin-top:24px}
.learn{left:630px;top:1076px;width:128px;height:38px}

/* benefits */
.benefits{left:0;top:1262px;width:1200px;height:459px;background:linear-gradient(110deg,#0a4ea8 0%,#0c56b3 45%,#1d68c4 70%,#0d55ae 100%)}
.benefits-title{left:143px;top:1366px;font-size:40px;color:var(--white)}
.benefit-list{left:143px;top:1424px;list-style:none}
.benefit-list li{display:flex;align-items:center;gap:14px;height:32px;font-size:18px;color:var(--white)}
.photo-ring{left:969px;top:1340px;width:116px;height:116px;border-radius:50%;background:var(--white)}
.photo-frame{left:667px;top:1364px;width:397px;height:426px;border-radius:26px;background:var(--navy)}
.benefit-photo{left:675px;top:1372px;width:381px;height:410px;border-radius:20px;background:linear-gradient(160deg,#c9d4d9 0%,#8f9aa0 40%,#5d5a55 75%,#3f3c3a 100%)}

/* pricing */
.pricing{left:0;top:1721px;width:1200px;height:746px;background:var(--sky)}
.pricing-title{left:0;width:1200px;top:1828px;text-align:center;font-size:40px;color:var(--white)}
.plan{width:278px;height:444px;top:1898px;border-radius:6px;background:var(--card);color:var(--white);text-align:center}
.plan.featured{height:451px;background:var(--white);color:var(--ink);box-shadow:0 6px 18px rgba(0,0,0,.15)}
.pill{display:inline-block;margin-top:30px;height:36px;padding:0 20px;line-height:36px;border-radius:18px;background:var(--navy);color:var(--white);font-size:15px;font-weight:500}
.plan.featured .pill{background:var(--sky)}
.plan-name{margin-top:14px;font-size:28px;font-weight:700}
.plan-sub{margin-top:4px;font-size:13px}
.plan.featured .plan-sub{color:var(--sky)}
.plan-price{margin-top:13px;height:53px;line-height:53px;font-size:29px;font-weight:700;background:rgba(255,255,255,.08)}
.plan.featured .plan-price{background:var(--ice);color:var(--navy)}
.plan-list{list-style:none;text-align:left;padding-left:34px;margin-top:14px}
.plan-list li{display:flex;align-items:center;gap:16px;height:32px;font-size:17.5px}
.plan.featured .plan-list li{color:var(--muted)}
.choose{left:537px;top:2332px;width:126px;height:36px;box-shadow:0 2px 6px rgba(0,0,0,.15)}

/* how it works */
.how-title{left:0;width:1200px;top:2552px;text-align:center;font-size:44px;color:var(--ink)}
.how-sub{left:0;width:1200px;top:2614px;text-align:center;font-size:20px;color:var(--ink)}
.step{width:284px;height:284px;border-radius:50%;border:2px solid var(--blue);top:2808px;text-align:center}
.step-num{left:112px;top:-22px;width:62px;height:62px;border-radius:50%;background:var(--navy);color:var(--white);font-size:17px;font-weight:500;display:flex;align-items:center;justify-content:center}
.step-icon{left:107px;top:62px}
.step-text{left:30px;right:30px;font-size:16px;line-height:24px;color:var(--ink)}

/* footer */
.site-footer{left:0;top:3202px;width:1200px;height:366px;background:linear-gradient(180deg,#2a2e33 0%,#15181c 55%,#0f1114 100%)}
.footer-brand{left:184px;top:3296px;color:var(--white);font-size:40px;gap:12px}
.footer-brand .brand-dot{width:46px;height:46px;border-color:var(--white);border-width:6px}
.social{top:3391px;width:30px;height:30px;border-radius:50%;border:1.5px solid var(--white);display:flex;align-items:center;justify-content:center}
.social.on{background:var(--white)}
.foot-head{top:3286px;font-family:"Lexend",sans-serif;font-size:20px;font-weight:500;color:var(--white)}
.foot-links{left:543px;top:3330px;list-style:none}
.foot-links li{display:flex;align-items:center;gap:12px;height:24px;font-size:15px;color:var(--white)}
.contact-item{left:783px;display:flex;align-items:center;gap:12px;font-size:15px;color:var(--white)}
.foot-rule{left:144px;top:3490px;width:911px;height:1px;background:rgba(255,255,255,.3)}
.copyright{left:0;width:1200px;top:3523px;text-align:center;font-size:12.5px;color:var(--white)}
</style>
</head>
<body>

<header class="site-header abs">
  <div class="brand header-brand abs"><span class="brand-dot"></span>PostNook</div>
  <nav class="nav">
    <span class="active-bar"></span>
    <a class="active" style="left:446px">HOME</a>
    <a style="left:517px">ABOUT US</a>
    <a style="left:614px">SERVICES</a>
    <a style="left:707px">BLOG</a>
    <a style="left:776px">CONTACT</a>
    <svg class="abs" style="left:881px;top:34px" width="15" height="15" viewBox="0 0 16 16"><circle cx="6.5" cy="6.5" r="4.5" fill="none" stroke="#2b2f36" stroke-width="2"/><line x1="10" y1="10" x2="14" y2="14" stroke="#2b2f36" stroke-width="2.4" stroke-linecap="round"/></svg>
  </nav>
  <div class="btn-outline quote abs">GET QUOTE</div>
</header>

<section class="hero abs" role="img" aria-label="Woman in glasses working at a laptop by a window"></section>
<div class="slide-arrow abs" style="top:304px"><svg width="12" height="8" viewBox="0 0 12 8"><path d="M2 6l4-4 4 4" fill="none" stroke="#2b2f36" stroke-width="1.6"/></svg></div>
<div class="slide-arrow abs" style="top:344px"><svg width="12" height="8" viewBox="0 0 12 8"><path d="M2 2l4 4 4-4" fill="none" stroke="#2b2f36" stroke-width="1.6"/></svg></div>
<div class="hero-box abs">
  <h1 class="hero-title display">POSTNOOK</h1>
  <div class="hero-cta abs">SIGN UP FOR A FREE TRIAL</div>
</div>

<section class="about">
  <svg class="abs" style="left:143px;top:720px" width="240" height="456" viewBox="0 0 240 456"><path d="M228 8 A220 220 0 0 0 228 448" fill="none" stroke="#0094D4" stroke-width="16"/></svg>
  <div class="about-photo abs" role="img" aria-label="Smiling woman in an orange sweater typing on a laptop"></div>
  <h2 class="about-title abs display">ABOUT US</h2>
  <div class="about-text abs">
    <p>There needs to be a super-admin panel where platform owner/administrator can see users, their activity, manage user access, etc.</p>
    <p>Each user will have a dashboard where they control their settings such as account information, billing, view blog posts, view blog post topics, etc. From this dashboard, the user can customize the “look and feel” of their blog including theme, hero banner, header, footer, logo, color scheme, etc.</p>
  </div>
  <div class="btn-outline learn abs">LEARN MORE</div>
</section>

<section class="benefits abs" role="img" aria-label="Blue architectural background"></section>
<h2 class="benefits-title abs display">OUR BENEFITS</h2>
<ul class="benefit-list abs">
  <li><svg width="16" height="16" viewBox="0 0 16 16"><circle cx="8" cy="8" r="8" fill="#fff"/><path d="M4.5 8.2l2.3 2.3 4.7-4.7" fill="none" stroke="#0054AA" stroke-width="2"/></svg>Lorem ipsum dolor sit amet, consectetur adipiscing</li>
  <li><svg width="16" height="16" viewBox="0 0 16 16"><circle cx="8" cy="8" r="8" fill="#fff"/><path d="M4.5 8.2l2.3 2.3 4.7-4.7" fill="none" stroke="#0054AA" stroke-width="2"/></svg>Duis aute irure dolor in reprehenderit in voluptate velit</li>
  <li><svg width="16" height="16" viewBox="0 0 16 16"><circle cx="8" cy="8" r="8" fill="#fff"/><path d="M4.5 8.2l2.3 2.3 4.7-4.7" fill="none" stroke="#0054AA" stroke-width="2"/></svg>Excepteur sint occaecat cupidatat non proident, sunt</li>
  <li><svg width="16" height="16" viewBox="0 0 16 16"><circle cx="8" cy="8" r="8" fill="#fff"/><path d="M4.5 8.2l2.3 2.3 4.7-4.7" fill="none" stroke="#0054AA" stroke-width="2"/></svg>Lorem ipsum dolor sit amet, consectetur adipiscing</li>
  <li><svg width="16" height="16" viewBox="0 0 16 16"><circle cx="8" cy="8" r="8" fill="#fff"/><path d="M4.5 8.2l2.3 2.3 4.7-4.7" fill="none" stroke="#0054AA" stroke-width="2"/></svg>Duis aute irure dolor in reprehenderit in voluptate velit</li>
  <li><svg width="16" height="16" viewBox="0 0 16 16"><circle cx="8" cy="8" r="8" fill="#fff"/><path d="M4.5 8.2l2.3 2.3 4.7-4.7" fill="none" stroke="#0054AA" stroke-width="2"/></svg>Excepteur sint occaecat cupidatat non proident, sunt</li>
</ul>

<section class="pricing abs"></section>
<div class="photo-ring abs"></div>
<div class="photo-frame abs"></div>
<div class="benefit-photo abs" role="img" aria-label="Smiling man in a blazer holding a tablet"></div>

<h2 class="pricing-title abs display">CHOOSE PRICING PLAN</h2>

<div class="plan abs" style="left:144px">
  <span class="pill">Base Plan</span>
  <div class="plan-name">1 blog post</div>
  <div class="plan-sub">(up to 2,000 words)</div>
  <div class="plan-price">$9.99/mo</div>
  <ul class="plan-list">
    <li><svg width="15" height="15" viewBox="0 0 16 16"><circle cx="8" cy="8" r="8" fill="#0054AA"/><path d="M4.5 8.2l2.3 2.3 4.7-4.7" fill="none" stroke="#fff" stroke-width="2"/></svg>Lorem ipsum dolor sit</li>
    <li><svg width="15" height="15" viewBox="0 0 16 16"><circle cx="8" cy="8" r="8" fill="#0054AA"/><path d="M4.5 8.2l2.3 2.3 4.7-4.7" fill="none" stroke="#fff" stroke-width="2"/></svg>Duis aute irure dolor</li>
    <li><svg width="15" height="15" viewBox="0 0 16 16"><circle cx="8" cy="8" r="8" fill="#0054AA"/><path d="M4.5 8.2l2.3 2.3 4.7-4.7" fill="none" stroke="#fff" stroke-width="2"/></svg>Excepteur sint occa</li>
    <li><svg width="15" height="15" viewBox="0 0 16 16"><circle cx="8" cy="8" r="8" fill="#0054AA"/><path d="M4.5 8.2l2.3 2.3 4.7-4.7" fill="none" stroke="#fff" stroke-width="2"/></svg>Lorem ipsum dolor sit</li>
    <li><svg width="15" height="15" viewBox="0 0 16 16"><circle cx="8" cy="8" r="8" fill="#0054AA"/><path d="M4.5 8.2l2.3 2.3 4.7-4.7" fill="none" stroke="#fff" stroke-width="2"/></svg>Duis aute irure dolor</li>
    <li><svg width="15" height="15" viewBox="0 0 16 16"><circle cx="8" cy="8" r="8" fill="#0054AA"/><path d="M4.5 8.2l2.3 2.3 4.7-4.7" fill="none" stroke="#fff" stroke-width="2"/></svg>Excepteur sint occa</li>
  </ul>
</div>

<div class="plan featured abs" style="left:461px">
  <span class="pill">Premium Plan</span>
  <div class="plan-name">1 blog post</div>
  <div class="plan-sub">(up to 2,000 words)</div>
  <div class="plan-price">$14.99/mo</div>
  <ul class="plan-list">
    <li><svg width="15" height="15" viewBox="0 0 16 16"><circle cx="8" cy="8" r="8" fill="#0054AA"/><path d="M4.5 8.2l2.3 2.3 4.7-4.7" fill="none" stroke="#fff" stroke-width="2"/></svg>Lorem ipsum dolor sit</li>
    <li><svg width="15" height="15" viewBox="0 0 16 16"><circle cx="8" cy="8" r="8" fill="#0054AA"/><path d="M4.5 8.2l2.3 2.3 4.7-4.7" fill="none" stroke="#fff" stroke-width="2"/></svg>Duis aute irure dolor</li>
    <li><svg width="15" height="15" viewBox="0 0 16 16"><circle cx="8" cy="8" r="8" fill="#0054AA"/><path d="M4.5 8.2l2.3 2.3 4.7-4.7" fill="none" stroke="#fff" stroke-width="2"/></svg>Excepteur sint occa</li>
    <li><svg width="15" height="15" viewBox="0 0 16 16"><circle cx="8" cy="8" r="8" fill="#0054AA"/><path d="M4.5 8.2l2.3 2.3 4.7-4.7" fill="none" stroke="#fff" stroke-width="2"/></svg>Lorem ipsum dolor sit</li>
    <li><svg width="15" height="15" viewBox="0 0 16 16"><circle cx="8" cy="8" r="8" fill="#0054AA"/><path d="M4.5 8.2l2.3 2.3 4.7-4.7" fill="none" stroke="#fff" stroke-width="2"/></svg>Duis aute irure dolor</li>
    <li><svg width="15" height="15" viewBox="0 0 16 16"><circle cx="8" cy="8" r="8" fill="#0054AA"/><path d="M4.5 8.2l2.3 2.3 4.7-4.7" fill="none" stroke="#fff" stroke-width="2"/></svg>Excepteur sint occa</li>
  </ul>
</div>
<div class="btn-outline choose abs">CHOOSE PLAN</div>

<div class="plan abs" style="left:777px">
  <span class="pill">Ultimate Plan</span>
  <div class="plan-name">1 blog post</div>
  <div class="plan-sub">(up to 3,000 words)</div>
  <div class="plan-price">$24.99/mo</div>
  <ul class="plan-list">
    <li><svg width="15" height="15" viewBox="0 0 16 16"><circle cx="8" cy="8" r="8" fill="#0054AA"/><path d="M4.5 8.2l2.3 2.3 4.7-4.7" fill="none" stroke="#fff" stroke-width="2"/></svg>Lorem ipsum dolor sit</li>
    <li><svg width="15" height="15" viewBox="0 0 16 16"><circle cx="8" cy="8" r="8" fill="#0054AA"/><path d="M4.5 8.2l2.3 2.3 4.7-4.7" fill="none" stroke="#fff" stroke-width="2"/></svg>Duis aute irure dolor</li>
    <li><svg width="15" height="15" viewBox="0 0 16 16"><circle cx="8" cy="8" r="8" fill="#0054AA"/><path d="M4.5 8.2l2.3 2.3 4.7-4.7" fill="none" stroke="#fff" stroke-width="2"/></svg>Excepteur sint occa</li>
    <li><svg width="15" height="15" viewBox="0 0 16 16"><circle cx="8" cy="8" r="8" fill="#0054AA"/><path d="M4.5 8.2l2.3 2.3 4.7-4.7" fill="none" stroke="#fff" stroke-width="2"/></svg>Lorem ipsum dolor sit</li>
    <li><svg width="15" height="15" viewBox="0 0 16 16"><circle cx="8" cy="8" r="8" fill="#0054AA"/><path d="M4.5 8.2l2.3 2.3 4.7-4.7" fill="none" stroke="#fff" stroke-width="2"/></svg>Duis aute irure dolor</li>
    <li><svg width="15" height="15" viewBox="0 0 16 16"><circle cx="8" cy="8" r="8" fill="#0054AA"/><path d="M4.5 8.2l2.3 2.3 4.7-4.7" fill="none" stroke="#fff" stroke-width="2"/></svg>Excepteur sint occa</li>
  </ul>
</div>

<section class="how">
  <h2 class="how-title abs display">HOW IT WORKS</h2>
  <p class="how-sub abs">The blog topics can be created using any of these methods:</p>
  <svg class="abs" style="left:0;top:2640px" width="1200" height="150" viewBox="0 0 1200 150">
    <g stroke="#0054AA" stroke-width="2.5" stroke-dasharray="2 6" stroke-linecap="round" fill="none">
      <line x1="290" y1="52" x2="590" y2="52"/>
      <line x1="608" y1="52" x2="905" y2="52"/>
      <line x1="599" y1="14" x2="599" y2="42"/>
      <line x1="282" y1="62" x2="282" y2="146"/>
      <line x1="599" y1="62" x2="599" y2="146"/>
      <line x1="914" y1="62" x2="914" y2="146"/>
    </g>
    <g fill="#0054AA" stroke="#7BADD7" stroke-width="3">
      <circle cx="282" cy="52" r="9"/><circle cx="599" cy="52" r="9"/><circle cx="914" cy="52" r="9"/>
    </g>
  </svg>

  <div class="step abs" style="left:141px">
    <div class="step-num abs">01</div>
    <svg class="step-icon abs" width="72" height="72" viewBox="0 0 72 72" fill="none" stroke="#0054AA" stroke-width="2.4" stroke-linecap="round" stroke-linejoin="round">
      <circle cx="28" cy="28" r="10"/>
      <path d="M28 6v7M28 43v7M6 28h7M43 28h7M12.5 12.5l5 5M38.5 38.5l5 5M12.5 43.5l5-5M38.5 17.5l5-5"/>
      <path d="M40 66V44a4 4 0 0 1 8 0v10l12 2a5 5 0 0 1 4 6l-1 4"/>
    </svg>
    <p class="step-text abs" style="top:166px">The user enters them into a table manually.</p>
  </div>

  <div class="step abs" style="left:458px">
    <div class="step-num abs">02</div>
    <svg class="step-icon abs" width="72" height="72" viewBox="0 0 72 72" fill="none" stroke="#0054AA" stroke-width="2.4" stroke-linecap="round" stroke-linejoin="round">
      <rect x="12" y="8" width="38" height="56" rx="4"/>
      <rect x="22" y="4" width="18" height="8" rx="2"/>
      <path d="M20 24h4M30 24h12M20 36h4M30 36h12M20 48h4M30 48h8"/>
      <path d="M44 60l16-16 5 5-16 16h-5z"/>
    </svg>
    <p class="step-text abs" style="top:166px;left:50px;right:50px">The user uploads a list of blog topics in CSV format.</p>
  </div>

  <div class="step abs" style="left:773px">
    <div class="step-num abs">03</div>
    <svg class="step-icon abs" width="72" height="66" viewBox="0 0 72 66" fill="none" stroke="#0054AA" stroke-width="2.4" stroke-linecap="round" stroke-linejoin="round">
      <rect x="6" y="24" width="52" height="32" rx="3"/>
      <path d="M2 60h62"/>
      <path d="M26 12h30a4 4 0 0 1 4 4v14a4 4 0 0 1-4 4H40l-8 7v-7h-6a4 4 0 0 1-4-4V16a4 4 0 0 1 4-4z"/>
      <path d="M32 22h18M32 28h12"/>
    </svg>
    <p class="step-text abs" style="top:136px">AI can create the list of blog topics based on a prompt such as: “Provide a list of 52 blog topics for a handyman business’s blog.”</p>
  </div>
</section>

<footer>
  <div class="site-footer abs" role="img" aria-label="Dark city skyline backdrop"></div>
  <div class="brand footer-brand abs"><span class="brand-dot"></span>PostNook</div>
  <div class="social abs" style="left:272px"><svg width="12" height="12" viewBox="0 0 12 12"><circle cx="6" cy="6" r="2" fill="#fff"/></svg></div>
  <div class="social on abs" style="left:318px"><svg width="12" height="12" viewBox="0 0 12 12"><rect x="2" y="2" width="8" height="8" rx="2" fill="none" stroke="#15181c" stroke-width="1.5"/></svg></div>

  <h3 class="foot-head abs" style="left:543px">Quick Links</h3>
  <ul class="foot-links abs">
    <li><svg width="11" height="11" viewBox="0 0 12 12"><circle cx="6" cy="6" r="5" fill="none" stroke="#0094D4" stroke-width="1.5"/><circle cx="6" cy="6" r="2" fill="#0094D4"/></svg>Home</li>
    <li><svg width="11" height="11" viewBox="0 0 12 12"><circle cx="6" cy="6" r="5" fill="none" stroke="#0094D4" stroke-width="1.5"/><circle cx="6" cy="6" r="2" fill="#0094D4"/></svg>About</li>
    <li><svg width="11" height="11" viewBox="0 0 12 12"><circle cx="6" cy="6" r="5" fill="none" stroke="#0094D4" stroke-width="1.5"/><circle cx="6" cy="6" r="2" fill="#0094D4"/></svg>Services</li>
    <li><svg width="11" height="11" viewBox="0 0 12 12"><circle cx="6" cy="6" r="5" fill="none" stroke="#0094D4" stroke-width="1.5"/><circle cx="6" cy="6" r="2" fill="#0094D4"/></svg>Blog</li>
    <li><svg width="11" height="11" viewBox="0 0 12 12"><circle cx="6" cy="6" r="5" fill="none" stroke="#0094D4" stroke-width="1.5"/><circle cx="6" cy="6" r="2" fill="#0094D4"/></svg>Contact</li>
  </ul>

  <h3 class="foot-head abs" style="left:783px">Contact Us</h3>
  <div class="contact-item abs" style="top:3331px"><svg width="12" height="16" viewBox="0 0 12 16"><path d="M6 0a6 6 0 0 0-6 6c0 4.5 6 10 6 10s6-5.5 6-10a6 6 0 0 0-6-6z" fill="#0094D4"/><circle cx="6" cy="6" r="2.2" fill="#15181c"/></svg>123, Lorem ipsum dolor sit</div>
  <div class="contact-item abs" style="top:3379px"><svg width="14" height="14" viewBox="0 0 14 14"><path d="M3 1l2.5 3-1.5 1.8a8 8 0 0 0 4.2 4.2L10 8.5l3 2.5-1.5 2A10 10 0 0 1 1 2.5z" fill="#0094D4"/></svg>+1 888 888 8888</div>
  <div class="contact-item abs" style="top:3427px"><svg width="16" height="12" viewBox="0 0 16 12"><rect width="16" height="12" rx="1.5" fill="#0094D4"/><path d="M1 1.5l7 5 7-5" fill="none" stroke="#15181c" stroke-width="1.4"/></svg>info@companyname</div>

  <div class="foot-rule abs"></div>
  <p class="copyright abs">© Copyrights 2024 | All Rights Reserved</p>
</footer>

</body>
</html>
```